NCBG website design

We need a page template website design for a cms website. Please see the brief attached for the details.
The client is the National Copperfleece Breeders Guild which is an organisation promoting the Copperfleece Sheep Breed within Australia.
Updates

Project Deadline Extended
Reason: So that my top few designs can make changes and re-submit.

Target Market(s)

See attached brief

```html
<!DOCTYPE html>
<html lang="en">
<head>
<meta charset="utf-8">
<title>National Copperfleece Breeders Guild</title>
<link href="https://fonts.googleapis.com/css2?family=Open+Sans:wght@400;600&family=Arvo&family=PT+Sans+Narrow:wght@700&display=swap" rel="stylesheet">
<style>
:root{
  --green:#119447;
  --green-dark:#0b6b31;
  --nav-top:#1aa652;
  --nav-bottom:#0e8a3f;
  --yellow:#f9c42a;
  --text:#6f6f6f;
  --heading:#1a9447;
  --footer:#333333;
  --page:#ffffff;
}
*{margin:0;padding:0;box-sizing:border-box}
html,body{width:985px;height:1200px;overflow:hidden;background:var(--page)}
body{position:relative;font-family:"Open Sans",Arial,sans-serif;color:var(--text)}
.site-header{position:absolute;left:0;top:0;width:985px;height:152px;background:linear-gradient(#f3f3f3,#fbfbfb)}
.brand{position:absolute;left:73px;top:38px;display:flex;align-items:center;gap:10px}
.brand-mark{width:56px;height:56px;border-radius:50%;background:var(--green)}
.brand-name{font-family:"Open Sans",Arial,sans-serif;font-weight:600;font-size:24px;color:var(--green)}
.org-title{position:absolute;left:320px;top:44px;font-family:"Arvo",Georgia,serif;font-size:22px;line-height:37px;color:var(--green);letter-spacing:.3px}
.search{position:absolute;left:700px;top:62px;width:215px;height:29px;border:1px solid #d6d6d6;background:#fff;font-size:12px;color:#888;padding:6px 10px}
.search svg{position:absolute;right:8px;top:8px}
.main-nav{position:absolute;left:0;top:152px;width:985px;height:48px;background:linear-gradient(var(--nav-top),var(--nav-bottom))}
.main-nav ul{list-style:none;display:flex;position:absolute;left:71px;top:0}
.main-nav li{height:48px;line-height:48px;text-align:center;font-family:Arial,sans-serif;font-weight:700;font-size:14px;color:#fff;text-shadow:0 1px 1px rgba(0,0,0,.45);border-right:1px solid rgba(0,0,0,.12);letter-spacing:-.2px}
.main-nav li.active{background:var(--yellow)}
.main-nav li.open{background:var(--green-dark)}
.dropdown{position:absolute;left:160px;top:212px;width:164px;height:82px;background:var(--green-dark);box-shadow:0 2px 4px rgba(0,0,0,.3);padding:12px 18px;font-size:12px;color:#d9eedf;z-index:3}
.dropdown::before{content:"";position:absolute;left:19px;top:-7px;border:7px solid transparent;border-top:0;border-bottom-color:var(--green-dark)}
.dropdown p{height:35px;line-height:20px}
.dropdown p:first-child{border-bottom:1px solid rgba(255,255,255,.3);margin:0 40px 0 0;height:27px}
.dropdown p+p{padding-top:8px}
.slider{position:absolute;left:71px;top:219px;width:843px;height:285px;background:#fff;box-shadow:0 1px 5px rgba(0,0,0,.25)}
.slide{position:absolute;left:8px;top:8px;width:826px;height:269px;background:linear-gradient(#8ea7b8 0%,#5d7a4c 30%,#4e7035 55%,#5f9a3c 80%,#5a8f3a 100%)}
.caption{position:absolute;left:8px;top:145px;width:380px;height:48px;background:rgba(20,30,20,.55);font-family:"PT Sans Narrow",Arial,sans-serif;font-size:26px;color:#fff;line-height:48px;padding-left:16px}
.dots{position:absolute;left:460px;top:260px;display:flex;gap:4px}
.dots i{width:14px;height:14px;border-radius:50%;background:rgba(255,255,255,.55)}
.dots i:first-child{background:#fff}
.features{position:absolute;left:71px;top:548px;width:843px;height:170px}
.feature{position:absolute;top:0;width:200px;text-align:center}
.feature .icon{width:76px;height:76px;margin:0 auto;border-radius:50%;border:1px solid var(--green);padding:4px}
.feature .icon span{display:flex;align-items:center;justify-content:center;width:66px;height:66px;border-radius:50%;background:var(--green)}
.feature h3{font-weight:400;font-size:18px;color:var(--heading);margin-top:14px}
.feature p{font-size:12px;line-height:21px;margin-top:6px;color:#666}
.divider{position:absolute;top:10px;width:12px;height:150px;background:radial-gradient(ellipse at left center,rgba(0,0,0,.12),rgba(0,0,0,0) 70%)}
.welcome{position:absolute;left:71px;top:776px;width:502px}
h2{font-weight:400;font-size:22px;color:var(--heading)}
.welcome p{font-size:12px;line-height:20.7px;margin-top:19px;color:#727272}
.welcome p+p{margin-top:9px}
.sponsors{position:absolute;left:629px;top:776px;width:285px}
.arrows{position:absolute;right:-2px;top:6px;display:flex;gap:6px}
.arrows span{width:20px;height:19px;background:#8a8a8a;display:flex;align-items:center;justify-content:center}
.sponsor-ad{position:absolute;left:7px;top:51px;width:276px;height:212px;background:linear-gradient(#dccaca,#cdbcbc)}
.site-footer{position:absolute;left:0;top:1100px;width:985px;height:100px;background:var(--footer);color:#fff;font-family:Arial,sans-serif;font-size:12px}
.footer-links{position:absolute;left:71px;top:29px}
.copyright{position:absolute;left:71px;top:59px}
.social{position:absolute;left:736px;top:36px;display:flex;gap:11px}
.social i{width:30px;height:30px}
</style>
</head>
<body>
<header class="site-header">
  <div class="brand"><span class="brand-mark"></span><span class="brand-name">Copperfleece</span></div>
  <h1 class="org-title">NATIONAL COPPERFLEECE<br>BREEDERS GUILD</h1>
  <div class="search">Search..
    <svg width="11" height="11" viewBox="0 0 11 11"><circle cx="4.5" cy="4.5" r="3.5" fill="none" stroke="#999" stroke-width="1.5"/><line x1="7" y1="7" x2="10" y2="10" stroke="#999" stroke-width="1.6"/></svg>
  </div>
</header>
<nav class="main-nav">
  <ul>
    <li class="active" style="width:79px">HOME</li>
    <li class="open" style="width:80px">ABOUT</li>
    <li style="width:87px">SEARCH</li>
    <li style="width:157px">MEMBER SERVICES</li>
    <li style="width:117px">STUD PAGES</li>
    <li style="width:74px">NEWS</li>
    <li style="width:76px">SALES</li>
    <li style="width:73px">LINKS</li>
    <li style="width:97px;border-right:0">CONTACT</li>
  </ul>
</nav>
<div class="dropdown"><p>Breed</p><p>Genetic Testing</p></div>
<section class="slider">
  <div class="slide" role="img" aria-label="Photo of a flock of sheep grazing on a green paddock with forested hills behind"></div>
  <div class="caption">PROIN GRAVIDA NIBH VEL VELIT</div>
  <div class="dots"><i></i><i></i><i></i><i></i></div>
</section>
<section class="features">
  <div class="feature" style="left:-7px">
    <div class="icon"><span><svg width="30" height="30" viewBox="0 0 24 24"><path fill="#fff" d="M6.6 10.8c1.4 2.8 3.8 5.1 6.6 6.6l2.2-2.2c.3-.3.7-.4 1-.2 1.1.4 2.3.6 3.6.6.6 0 1 .4 1 1V20c0 .6-.4 1-1 1C10.6 21 3 13.4 3 4c0-.6.4-1 1-1h3.5c.6 0 1 .4 1 1 0 1.3.2 2.5.6 3.6.1.3 0 .7-.2 1z"/><path fill="none" stroke="#fff" stroke-width="1.6" d="M14 3a7 7 0 0 1 7 7M14 6.5a3.5 3.5 0 0 1 3.5 3.5"/></svg></span></div>
    <h3>Prime Lamb Helpline</h3><p>Typi non habent claritatem<br>insitam; est legentis</p>
  </div>
  <div class="divider" style="left:202px"></div>
  <div class="feature" style="left:214px">
    <div class="icon"><span><svg width="30" height="30" viewBox="0 0 24 24" fill="none" stroke="#fff" stroke-width="1.6"><rect x="3" y="5" width="18" height="16" rx="1"/><line x1="3" y1="9" x2="21" y2="9"/><line x1="8" y1="3" x2="8" y2="7"/><line x1="16" y1="3" x2="16" y2="7"/><g fill="#fff" stroke="none"><rect x="6" y="11" width="2.5" height="2"/><rect x="10.7" y="11" width="2.5" height="2"/><rect x="15.4" y="11" width="2.5" height="2"/><rect x="6" y="15" width="2.5" height="2"/><rect x="10.7" y="15" width="2.5" height="2"/><rect x="15.4" y="15" width="2.5" height="2"/></g></svg></span></div>
    <h3>Events</h3><p>Typi non habent claritatem<br>insitam; est legentis</p>
  </div>
  <div class="divider" style="left:429px"></div>
  <div class="feature" style="left:445px">
    <div class="icon"><span><svg width="30" height="30" viewBox="0 0 24 24" fill="#fff"><circle cx="12" cy="8" r="4.5"/><path d="M3 22c0-5 4-8 9-8s9 3 9 8z"/></svg></span></div>
    <h3>Members</h3><p>Typi non habent claritatem<br>insitam; est legentis</p>
  </div>
  <div class="divider" style="left:658px"></div>
  <div class="feature" style="left:660px">
    <div class="icon"><span><svg width="32" height="30" viewBox="0 0 26 24" fill="none" stroke="#fff" stroke-width="1.6"><rect x="4" y="4" width="19" height="16"/><path d="M4 8H2v10a2 2 0 0 0 2 2"/><rect x="7" y="7" width="6" height="5" fill="#fff" stroke="none"/><line x1="15" y1="8" x2="20" y2="8"/><line x1="15" y1="11" x2="20" y2="11"/><line x1="7" y1="14.5" x2="20" y2="14.5"/><line x1="7" y1="17" x2="20" y2="17"/></svg></span></div>
    <h3>News</h3><p>Typi non habent claritatem<br>insitam; est legentis</p>
  </div>
</section>
<section class="welcome">
  <h2>Welcome to our website</h2>
  <p>Mirum est notare quam littera gothica, quam nunc putamus parum claram, anteposuerit litterarum formas humanitatis per seacula quarta decima et quinta decima. Nam liber tempor cum soluta nobis eleifend option congue nihil imperdiet doming id quod mazim placer at facer possim assum. Typi non habent claritatem insitam; est usus legentis in iis qiui facit eorum claritatem. Investigationes demonstraverunt lectores legere me lius.</p>
  <p>Nam liber tempor cum soluta nobis eleifend option conngue nihil imperdiet doming id quiod mazim placerat facer possim assum. Typi non habent claritatem insitam; est usus legentis in iis qui facit eorum claritatem. Investigationes demonstraverunt lectores legere me lius quod ii legunt saepius. Claritas est etiam processus dynamicus, qui sequitur mutationem consuetudium lectorum. Mirum est notare quam littera gothica</p>
</section>
<aside class="sponsors">
  <h2>Sponsers</h2>
  <div class="arrows">
    <span><svg width="6" height="10" viewBox="0 0 6 10"><path d="M5 1L1 5l4 4" fill="none" stroke="#fff" stroke-width="1.3"/></svg></span>
    <span><svg width="6" height="10" viewBox="0 0 6 10"><path d="M1 1l4 4-4 4" fill="none" stroke="#fff" stroke-width="1.3"/></svg></span>
  </div>
  <div class="sponsor-ad" role="img" aria-label="Sponsor advert for Redgum Cattle Co offering bull semen for sale, with a photo of the bull Kelvale Drover K112"></div>
</aside>
<footer class="site-footer">
  <p class="footer-links">Home | About | Search | Member Services | Stud Pages | News | Sales | Links | Contact</p>
  <p class="copyright">Copyright © 2013. All Rights Reserved.</p>
  <div class="social">
    <i style="background:#3b5bad"></i>
    <i style="background:#2f9fd8"></i>
    <i style="background:#f36f21"></i>
    <i style="background:#e02a2a"></i>
  </div>
</footer>
</body>
</html>
```